Real Estate Team Business Card

We need a business card designed for our real estate team called "Maplecrest Realty Group". We would like to receive a final format that would allow us to edit the contact information for new employees as they are added to our team. The difficult part of the design is that we will need to have two logos on the card - both our team name logo for "Maplecrest Realty Group" and our company logo for "Summitpoint Real Estate". Most emphasis should be given to the team logo - maybe double the size of our company logo. (we just have to have the company logo somewhere on the card for legal purposes) The design should somehow illustrate we work in real estate, but still use the beehive/bee concept as a lot of our marketing will involve "bee" sayings. We would also like to use the tagline: "find out what all the buzz is about". We also need to use the "fair housing" logo and "realtor" logos. These can both be small like the company logo.
Target Market(s)
Real Estate
Industry/Entity Type
Real Estate Agent
Contact Information for Business Card
Name: Darren Pulaski Title: Realtor Phone: 801-372-5518 Email: darren@maplecrestrealtrygroup.com Website: www.maplecrestrealtygroup.com Facebook: fb/me/maplecrestrealtygroup Twitter: @MaplecrestRltyGrp
Colors
Designer to choose colors to be used in the design.
Requirements
Must have
- Contact information. Maplecrest Realty Group Logo. Summitpoint Real Estate Logo. Realtor logo. Fair Housing Logo. Tagline: "find out what all the buzz is about".
Nice to have
- It would be nice to illustrate that we work in real estate. It would also be nice to somehow incorporate bees or play off of our beehive logo. We will do a lot of marking using sayings like "let us bee the solution" or "real estate meant to bee" etc.

```html
<!DOCTYPE html>
<html lang="en">
<head>
<meta charset="utf-8">
<title>Maplecrest Realty Group – Business Card</title>
<link rel="stylesheet" href="https://fonts.googleapis.com/css2?family=Montserrat:wght@400;600;700&family=Open+Sans:wght@400;600;700&family=Libre+Baskerville&display=swap">
<style>
  :root {
    --stage: #1f1f1f;
    --ink: #120806;
    --paper: #e4e3df;
    --honey: #d6a508;
    --honey-soft: #e0b21a;
    --cream: #f2efe6;
    --brown: #3a2218;
  }
  * { box-sizing: border-box; margin: 0; padding: 0; }
  html, body { width: 1200px; height: 900px; overflow: hidden; }
  body {
    background: var(--stage);
    font-family: "Open Sans", sans-serif;
    position: relative;
  }
  .card {
    position: absolute;
    left: 300px;
    width: 600px;
    height: 343px;
    overflow: hidden;
    border-radius: 4px;
    box-shadow: 0 10px 30px rgba(0,0,0,.45);
  }
  .card--front { top: 80px; background: var(--paper); }
  .card--back { top: 477px; background: var(--ink); }

  .front-shapes { position: absolute; inset: 0; }

  .partner-row {
    position: absolute;
    top: 14px; left: 28px;
    display: flex; align-items: center; gap: 16px;
  }
  .partner-name {
    font-family: "Montserrat", sans-serif;
    font-weight: 600;
    font-size: 13px;
    color: var(--brown);
    letter-spacing: .3px;
  }
  .badge {
    width: 26px; height: 26px;
    background: var(--brown);
    border-radius: 3px;
  }

  .agent {
    position: absolute;
    top: 84px; left: 36px;
    color: var(--honey);
  }
  .agent-name {
    font-family: "Open Sans", sans-serif;
    font-weight: 700;
    font-size: 20px;
  }
  .agent-title {
    font-family: "Libre Baskerville", serif;
    font-size: 16px;
    color: var(--cream);
    margin-top: 2px;
  }
  .contact-list {
    list-style: none;
    margin-top: 22px;
    display: flex; flex-direction: column; gap: 9px;
  }
  .contact-item {
    display: flex; align-items: center; gap: 14px;
    font-family: "Open Sans", sans-serif;
    font-size: 12.5px;
    font-weight: 600;
    letter-spacing: 1.4px;
  }
  .contact-item--phone { letter-spacing: 4px; }
  .contact-icon {
    width: 15px; height: 15px; flex: none;
    border-radius: 50%;
    background: var(--honey);
    display: flex; align-items: center; justify-content: center;
  }

  .team-logo {
    position: absolute;
    right: 26px; top: 140px;
    display: flex; flex-direction: column; align-items: center; gap: 8px;
  }
  .team-mark {
    width: 34px; height: 34px;
    background: var(--honey);
    border-radius: 3px;
  }
  .team-name {
    font-family: "Montserrat", sans-serif;
    font-weight: 700;
    font-size: 16px;
    line-height: 1.15;
    color: var(--brown);
    letter-spacing: 1px;
    text-transform: uppercase;
    text-align: center;
  }

  .band {
    position: absolute; left: 0; right: 0;
    height: 56px;
    background: var(--honey);
  }
  .band--top { top: 0; }
  .band--bottom { bottom: 0; }
  .website {
    position: absolute;
    top: 50%; left: 0; right: 0;
    transform: translateY(-50%);
    text-align: center;
    font-family: "Montserrat", sans-serif;
    font-weight: 700;
    font-size: 20px;
    color: var(--honey-soft);
    letter-spacing: .5px;
  }
</style>
</head>
<body>

  <section class="card card--front" aria-label="Business card front">
    <svg class="front-shapes" width="600" height="343" viewBox="0 0 600 343" aria-hidden="true">
      <polygon fill="var(--honey)" points="0,52 366,52 462,343 444,343 352,62 0,62"/>
      <polygon fill="var(--ink)" points="0,62 352,62 444,343 0,343"/>
    </svg>

    <div class="partner-row">
      <span class="partner-name">Summitpoint Real Estate</span>
      <span class="badge" aria-label="Realtor badge"></span>
      <span class="badge" aria-label="Fair housing badge"></span>
    </div>

    <div class="agent">
      <h1 class="agent-name">Darren Pulaski</h1>
      <p class="agent-title">Realtor</p>
      <ul class="contact-list">
        <li class="contact-item contact-item--phone">
          <span class="contact-icon">
            <svg width="9" height="9" viewBox="0 0 24 24"><path fill="var(--ink)" d="M6.6 10.8a15 15 0 0 0 6.6 6.6l2.2-2.2c.3-.3.7-.4 1-.2 1.1.4 2.3.6 3.6.6.6 0 1 .4 1 1V20c0 .6-.4 1-1 1A17 17 0 0 1 3 4c0-.6.4-1 1-1h3.5c.6 0 1 .4 1 1 0 1.3.2 2.5.6 3.6.1.3 0 .7-.2 1z"/></svg>
          </span>801-372-5518</li>
        <li class="contact-item">
          <span class="contact-icon">
            <svg width="9" height="9" viewBox="0 0 24 24"><path fill="var(--ink)" d="M2 5h20v14H2z M2 5l10 8 10-8" stroke="var(--honey)" stroke-width="1.5"/></svg>
          </span>darren@maplecrestrealtrygroup.com</li>
        <li class="contact-item"><span class="contact-icon"></span>fb/me/maplecrestrealtygroup</li>
        <li class="contact-item"><span class="contact-icon"></span>@MaplecrestRltyGrp</li>
      </ul>
    </div>

    <div class="team-logo">
      <span class="team-mark" aria-hidden="true"></span>
      <span class="team-name">Maplecrest<br>Realty Group</span>
    </div>
  </section>

  <section class="card card--back" aria-label="Business card back">
    <div class="band band--top"></div>
    <p class="website">www.maplecrestrealtygroup.com</p>
    <div class="band band--bottom"></div>
  </section>

</body>
</html>
```